Local fast-growing company in the service sector

We are looking for a modern business card design, which should also appear on our letterheads

Target Market(s)

Private and industrial sectors

Contact Information for Business Card

Vorname Name
Kellberger Str. 18
72816 Kellbach
Tel.: 07146-839214-0
Name@agentur-kvtl.de

Colors
9d9d9d
919191
aaaaaa

Requirements
Must have
• The logo (file) in silver

```html
<!DOCTYPE html>
<html lang="de">
<head>
<meta charset="utf-8">
<title>KVTL Visitenkarte</title>
<link href="https://fonts.googleapis.com/css2?family=Lato:wght@400;700&display=swap" rel="stylesheet">
<style>
  :root {
    --backdrop: #e6e6e6;
    --card-white: #f4f4f4;
    --silver: #9d9d9d;
    --silver-dark: #919191;
    --silver-light: #aaaaaa;
    --ink-light: #ffffff;
    --ink-soft: #eeeeee;
  }
  html, body {
    margin: 0;
    width: 1200px;
    height: 997px;
    overflow: hidden;
    background: var(--backdrop);
    font-family: "Lato", sans-serif;
  }
  .business-card {
    position: absolute;
    left: 150px;
    top: 241px;
    width: 900px;
    height: 515px;
    display: flex;
    background: var(--card-white);
    box-shadow: 0 10px 30px rgba(0,0,0,0.18);
    overflow: hidden;
  }
  .brand-side {
    width: 360px;
    display: flex;
    align-items: center;
    justify-content: center;
    background: linear-gradient(160deg, #fafafa, #ececec);
  }
  .brand-mark {
    display: flex;
    align-items: center;
    gap: 18px;
  }
  .brand-square {
    width: 46px;
    height: 46px;
    background: var(--silver);
  }
  .brand-name {
    font-weight: 700;
    font-size: 64px;
    letter-spacing: 2px;
    color: var(--silver-dark);
  }
  .divider-stripes {
    width: 38px;
    display: flex;
    gap: 7px;
    padding-left: 4px;
    box-sizing: border-box;
  }
  .divider-stripes span {
    width: 6px;
    background: var(--silver-light);
  }
  .contact-side {
    flex: 1;
    background: linear-gradient(160deg, var(--silver-light), var(--silver-dark));
    color: var(--ink-light);
    padding: 92px 0 0 70px;
    box-sizing: border-box;
  }
  .contact-name {
    font-weight: 700;
    font-size: 26px;
    margin: 0;
  }
  .contact-role {
    font-size: 17px;
    color: var(--ink-soft);
    margin: 4px 0 34px;
  }
  .contact-line {
    display: flex;
    align-items: center;
    gap: 14px;
    font-size: 22px;
    margin-bottom: 16px;
  }
  .contact-icon {
    width: 26px;
    height: 26px;
    flex: none;
  }
  .contact-address {
    font-weight: 700;
    font-size: 24px;
    line-height: 1.45;
    margin-top: 30px;
  }
</style>
</head>
<body>
  <article class="business-card">
    <section class="brand-side">
      <div class="brand-mark">
        <div class="brand-square"></div>
        <div class="brand-name">KVTL</div>
      </div>
    </section>
    <div class="divider-stripes"><span></span><span></span></div>
    <section class="contact-side">
      <h1 class="contact-name">Henrike Vollmer</h1>
      <p class="contact-role">KVTL Agentur</p>
      <div class="contact-line">
        <svg class="contact-icon" viewBox="0 0 26 26" aria-hidden="true">
          <circle cx="13" cy="13" r="13" fill="#bdbdbd"/>
          <path d="M7 9c0-1 1-2 2-2h8c1 0 2 1 2 2v1h-3v-1h-6v1H7z M8 11h10l1 7H7z" fill="#8a8a8a"/>
          <circle cx="13" cy="15" r="1.8" fill="#bdbdbd"/>
        </svg>
        <span>07146-839214-0</span>
      </div>
      <div class="contact-line">
        <svg class="contact-icon" viewBox="0 0 26 26" aria-hidden="true">
          <circle cx="13" cy="13" r="13" fill="#bdbdbd"/>
          <rect x="7" y="9" width="12" height="8" fill="#8a8a8a"/>
          <path d="M7 9l6 5 6-5" fill="none" stroke="#bdbdbd" stroke-width="1.2"/>
        </svg>
        <span>Name@agentur-kvtl.de</span>
      </div>
      <div class="contact-address">
        Kellberger Str. 18<br>
        72816 Kellbach
      </div>
    </section>
  </article>
</body>
</html>
```